HAIR EXTENSIONS

We need a web design for a company base in Chicago called Tresses by Jolavie. We sale 100% human hair in Brazilian body wave deep wave straight or natural curl, Peruvian body wave straight or deep wave. Malaysian loose straight or body wave, in the chicago land.
We also ship hair to any city or country. We like to see design that use the colors pinks & grays, or would just like to see some design creative with colors thats inviting.

Also I'm using the quillmoss template, Home- banner contact us, about us, Features- product side/left sidebar, Shop- wish list /shopping cart/ tracking your order / checkout/ order received.
Porfolio-filterable 4column portfolio
Blog. Buy now

Industry/Entity Type

Hair

Number of Pages Required

4 page

Colors
aaaaaa
606060
dddddd
eea4c8
d3a5cc
b868aa
a6459a
ffc213
1b1b1b

Requirements
Must have
• I NEED THE DESIGNER TO DO THE 4 PAGE LIKE THIS.
• 1.HOME-PAGE BANNER CONTACT US SOME PRODUCT WITH SIDING IMAGES OF THE TOP PROUDCT
• 2.PRODUCT WITH SHOPPING CART- I WANT SIDING BARS FOR PRODUCT & SHOPPING CART WITH TRACKING YOUR ORDERS CHECK OUT & ORDER RECEIVED.
• 3.PORFOLIO PHOTO-I WANT A FEATURES FOR CUSTOMERS TO UPLOAN THERE PICTURE & BLOG ON THE PAGE
• 4.ABOUT US- TALK ABOUT ARE COMPAMY.
Nice to have
• hello designer
• I was working with a web developer for my site be for i came to craftnookly & they build a site for me that i liked, You all can view it at www.Tressesbyjolavie.info
• long story short never could get them to finish the project after they got paid!!
• I know, why paid before its finish bad decision. So know I'm here starting over with you all.
• here is a list of my competition site
• www.lockswellhub.com
• www.vanoraloft.com
• www.pellinoshop.com
• So just to give some insight, I'm looking for something like the one i had builded.

```html
<!DOCTYPE html>
<html lang="en">
<head>
<meta charset="utf-8">
<title>Tresses by Jolavie — Home</title>
<link href="https://fonts.googleapis.com/css2?family=Open+Sans:wght@400;600&family=Questrial&family=Oswald:wght@500&display=swap" rel="stylesheet">
<style>
:root{
  --bg:#fdfdfd;
  --ink:#5f5f5f;
  --ink-soft:#8a8a8a;
  --line:#dddddd;
  --accent:#ee8e6c;
  --accent-deep:#c8512f;
  --link:#1aa6d6;
  --hero:#3a2a2e;
  --dark:#1b1b1b;
  --photo-pink:#e85aa0;
}
*{box-sizing:border-box;margin:0;padding:0}
html,body{width:848px;height:1200px;overflow:hidden;background:var(--bg)}
body{position:relative;font-family:"Open Sans",sans-serif;color:var(--ink)}
.abs{position:absolute}
.brand{left:0;width:848px;top:18px;text-align:center;font-family:"Questrial",sans-serif;font-size:40px;color:var(--accent);line-height:1}
.tagline{left:325px;width:198px;top:72px;height:25px;border-top:1px solid var(--line);border-bottom:1px solid var(--line);text-align:center;font-size:10px;letter-spacing:3.2px;line-height:23px;color:var(--ink-soft)}
.account{left:71px;top:78px;font-size:9px;color:var(--ink)}
.account span{color:#bbb;margin:0 5px}
.cart{left:710px;top:73px;display:flex;align-items:center;gap:6px;font-size:11px}
.cart .ring{width:26px;height:26px;border:1px solid var(--line);border-radius:50%;display:flex;align-items:center;justify-content:center}
.nav{left:71px;top:125px;width:707px;height:42px;border:1px solid var(--line);display:flex;font-size:10.5px;color:var(--ink-soft)}
.nav a{display:flex;align-items:center;justify-content:center;border-right:1px solid var(--line);text-decoration:none;color:inherit}
.nav a.active{background:#f3f3f3}
.nav .search{flex:1;justify-content:space-between;padding:0 18px 0 28px;border:none}
.hero{left:71px;top:177px;width:707px;height:329px;background:var(--hero);overflow:hidden}
.hero .photo{position:absolute;left:0;top:0;width:460px;height:329px;background:linear-gradient(100deg,#4a3535 0%,var(--photo-pink) 35%,#5a3d3a 55%,var(--photo-pink) 80%,#3a2a2e 100%)}
.hero .kicker{position:absolute;right:22px;top:93px;color:#fff;font-size:13px}
.hero h1{position:absolute;right:22px;top:112px;font-family:"Oswald",sans-serif;font-weight:500;font-size:36px;color:var(--accent);letter-spacing:.5px}
.hero .btn{position:absolute;left:587px;top:167px;width:96px;height:40px;border:2px solid #e8e8e8;color:#fff;font-size:12px;display:flex;align-items:center;justify-content:center}
.hero .dots{position:absolute;left:611px;top:233px;width:72px;height:16px;background:var(--dark);border-radius:8px;display:flex;align-items:center;justify-content:center;gap:7px}
.hero .dots i{width:7px;height:7px;border-radius:50%;background:#fff}
.hero .dots i.on{background:none;border:1.5px solid #fff}
.promo{top:516px;height:101px;border:1px solid var(--line);padding:12px 18px}
.promo h2{font-family:"Questrial",sans-serif;font-weight:400;font-size:31px;line-height:1.1;white-space:nowrap}
.promo p{font-size:11px;line-height:16px;margin-top:7px;color:var(--ink)}
.promo-a{left:72px;width:347px}
.promo-a h2{color:var(--accent)}
.promo-a p{text-align:center}
.promo-a a{color:var(--accent-deep);text-decoration:none}
.promo-b{left:430px;width:348px}
.promo-b h2{color:#555}
.section-title{left:71px;font-family:"Oswald",sans-serif;font-weight:500;font-size:20px;color:#555}
.pager{left:744px;display:flex;gap:2px}
.card{top:682px;width:168px;height:204px;border:1px solid var(--line);text-align:center;font-size:10px}
.card .ph{margin:5px 5px 0;height:148px}
.card p{margin-top:15px}
.card svg{margin-top:5px}
.rule{left:71px;width:707px;height:1px;background:var(--line)}
.feed-ph{left:72px;top:971px;width:118px;height:99px;background:linear-gradient(135deg,#c9b49a,#5a3a30 55%,#d9507a)}
.feed{left:202px;top:969px;width:560px;font-size:10.5px;line-height:16px}
.feed a{color:var(--link);text-decoration:none}
.meta{left:202px;top:1026px;font-size:10.5px;color:var(--link)}
.actions{left:207px;top:1058px;display:flex;gap:27px}
.foot-links{left:71px;top:1119px;font-size:10px}
.foot-links span{margin:0 8px}
.copy{left:71px;top:1140px;font-size:10px}
.social{left:71px;top:1167px;display:flex;gap:10px}
.social i{width:10px;height:11px;background:#9a9a9a}
.news-label{left:618px;top:1119px;font-size:10px}
.news{left:618px;top:1142px;width:159px;height:27px;border:1px solid var(--line);display:flex}
.news span{flex:1;font-size:9.5px;color:#aaa;padding:7px 9px}
.news b{width:26px;background:#ddd;display:flex;align-items:center;justify-content:center}
</style>
</head>
<body>
<div class="abs brand">byJolavie</div>
<div class="abs tagline">100% HUMAN HAIR</div>
<div class="abs account">My Account<span>/</span>Checkour<span>/</span>Logout</div>
<div class="abs cart"><div class="ring"><svg width="11" height="9" viewBox="0 0 11 9"><path d="M0 3h11L9.5 9h-8z" fill="#888"/><path d="M3 3l2-3M8 3L6 0" stroke="#888" fill="none"/></svg></div>$00.00</div>

<nav class="abs nav">
  <a class="active" style="width:81px">HOME</a>
  <a style="width:87px">ABOUT</a>
  <a style="width:101px">PRODUCT</a>
  <a style="width:93px">GALLERY</a>
  <a style="width:92px">CONTACT</a>
  <a class="search">SEARCH<svg width="10" height="10" viewBox="0 0 10 10"><circle cx="4" cy="4" r="3" stroke="#aaa" fill="none" stroke-width="1.4"/><path d="M6.5 6.5L9.5 9.5" stroke="#aaa" stroke-width="1.4"/></svg></a>
</nav>

<section class="abs hero">
  <div class="photo" role="img" aria-label="Two photos of a smiling woman in a pink blazer showing off long hair extensions"></div>
  <div class="kicker">Pellentesque viverra</div>
  <h1>PELLENTESQUE</h1>
  <div class="btn">VIEW MORE</div>
  <div class="dots"><i class="on"></i><i></i><i></i><i></i></div>
</section>

<div class="abs promo promo-a"><h2>TRESSES by JOLAVIE</h2><p>100% virgin Peruvian and Brazilian human hair.<br><a>Contact</a> for a great price! Quality and affordable.</p></div>
<div class="abs promo promo-b"><h2>Vivamus quam turpis</h2><p>Aenean nibh diam, venenatis in nunc id, venenatis imperdiet mauris. Curabitur vel hendrerit tortor.</p></div>

<h3 class="abs section-title" style="top:644px">OUR PRODUCT</h3>
<div class="abs pager" style="top:649px">
  <svg width="16" height="16" viewBox="0 0 16 16"><circle cx="8" cy="8" r="7" fill="none" stroke="#999"/><path d="M11 8H5M7.5 5.5L5 8l2.5 2.5" stroke="#999" fill="none"/></svg>
  <svg width="16" height="16" viewBox="0 0 16 16"><circle cx="8" cy="8" r="7" fill="none" stroke="#999"/><path d="M5 8h6M8.5 5.5L11 8l-2.5 2.5" stroke="#999" fill="none"/></svg>
</div>

<div class="abs card" style="left:72px"><div class="ph" role="img" aria-label="Customer with long dark wavy hair in a kitchen" style="background:linear-gradient(160deg,#b5703a,#2a2630 60%,#8a4a2a)"></div><p>Pellentesque</p><svg width="10" height="8" viewBox="0 0 11 9"><path d="M0 3h11L9.5 9h-8z" fill="#888"/><path d="M3 3l2-3M8 3L6 0" stroke="#888" fill="none"/></svg></div>
<div class="abs card" style="left:251px"><div class="ph" role="img" aria-label="Customer with braided hair" style="background:linear-gradient(180deg,#f2d6e2,#4a2e28 50%,#e8c8d6)"></div><p>Pellentesque</p><svg width="10" height="8" viewBox="0 0 11 9"><path d="M0 3h11L9.5 9h-8z" fill="#888"/><path d="M3 3l2-3M8 3L6 0" stroke="#888" fill="none"/></svg></div>
<div class="abs card" style="left:430px"><div class="ph" role="img" aria-label="Two customers with long straight hair" style="background:linear-gradient(135deg,#e4ddd6,#3a2824 55%,#6a4236)"></div><p>Pellentesque</p><svg width="10" height="8" viewBox="0 0 11 9"><path d="M0 3h11L9.5 9h-8z" fill="#888"/><path d="M3 3l2-3M8 3L6 0" stroke="#888" fill="none"/></svg></div>
<div class="abs card" style="left:610px"><div class="ph" role="img" aria-label="Customer with red-tinted bob hairstyle" style="background:linear-gradient(150deg,#8a2a34,#5a3a30 45%,#ece8e4)"></div><p>Pellentesque</p><svg width="10" height="8" viewBox="0 0 11 9"><path d="M0 3h11L9.5 9h-8z" fill="#888"/><path d="M3 3l2-3M8 3L6 0" stroke="#888" fill="none"/></svg></div>

<div class="abs rule" style="top:920px"></div>
<h3 class="abs section-title" style="top:933px">SOCIAL FEEDS</h3>
<div class="abs pager" style="top:938px">
  <svg width="16" height="16" viewBox="0 0 16 16"><circle cx="8" cy="8" r="7" fill="none" stroke="#999"/><path d="M11 8H5M7.5 5.5L5 8l2.5 2.5" stroke="#999" fill="none"/></svg>
  <svg width="16" height="16" viewBox="0 0 16 16"><circle cx="8" cy="8" r="7" fill="none" stroke="#999"/><path d="M5 8h6M8.5 5.5L11 8l-2.5 2.5" stroke="#999" fill="none"/></svg>
</div>
<div class="abs feed-ph" role="img" aria-label="Two friends posing together"></div>
<p class="abs feed">Maecenas at augue maximus, rutrum <a>augue sed, imperdiet</a> ipsum. Nulla mattis elementum sem eget bibendum. Nulla a neque et orci fermentum facilisis vitae vitae eros. Maecenas volutpat blandit ipsum, nec dapibus felis volut-pat sed. Pellentesque aliquam, justo sit amet vehicula egestas</p>
<div class="abs meta">Dalisa Reyne @DalisaReyne &nbsp;·&nbsp; May 4, 2014</div>
<div class="abs actions">
  <svg width="12" height="10" viewBox="0 0 12 10"><path d="M5 0L0 4.5 5 9V6c3 0 5 1 7 4-1-4-3-6-7-6z" fill="#c5c5c5"/></svg>
  <svg width="14" height="10" viewBox="0 0 14 10"><path d="M2 8V2h7M12 2v6H5" stroke="#c5c5c5" stroke-width="2" fill="none"/><path d="M0 7l2 3 2-3zM10 3l2-3 2 3z" fill="#c5c5c5"/></svg>
  <svg width="11" height="11" viewBox="0 0 12 12"><path d="M6 0l1.8 4 4.2.4-3.2 2.8 1 4.2L6 9.2 2.2 11.4l1-4.2L0 4.4 4.2 4z" fill="#c5c5c5"/></svg>
  <svg width="14" height="10" viewBox="0 0 14 10"><circle cx="2" cy="5" r="1.6" fill="#c5c5c5"/><circle cx="7" cy="5" r="1.6" fill="#c5c5c5"/><circle cx="12" cy="5" r="1.6" fill="#c5c5c5"/></svg>
</div>

<div class="abs rule" style="top:1090px"></div>
<div class="abs foot-links">Home<span>|</span>About<span>|</span>Product<span>|</span>Gallery<span>|</span>Contact</div>
<div class="abs copy">Copyright © 2014 &nbsp;byJolavie. &nbsp;All rights reserved.</div>
<div class="abs social"><i></i><i></i></div>
<div class="abs news-label">Newsletter Signup</div>
<div class="abs news"><span>E-mail</span><b><svg width="10" height="10" viewBox="0 0 10 10"><path d="M0 5h8M5 1.5L8.5 5 5 8.5" stroke="#fff" stroke-width="2" fill="none"/></svg></b></div>
</body>
</html>
```